Aquavelo- plumbing service flyer

Hello,
We would like to create flyer for our plumbing company Aquavelo
- we have 2 web domains
aquavelo-example.hr ( official)
preuredjenjedoma-example.hr ( for bathroom renovation)

- we would like to create a similar Z-fold flyer ( from A4 paper) for our services
- We are sending images used on our websites. Of Course, it is allowed to put some of their own. Depending on design
- sending word with text which should go on each page. Text can be modified but in the sense of a page. The massage on a page should be as in word.
What is important to us:
- to stay in blue color
- It should be 1 page when fully open. So it looks like the complete page of information
- first/front page should be with our logo and phone number. more focus on emergency plumbing.
- back page should be about bathroom remodeling. Not necessary but would be received more points
- please don't use images of regular plumbers from Pixelvault and similar. we don't want to use this stock's regular images as all others.

Target Market(s)

Bathroom remodeling and emergency plumbing

Industry/Entity Type

Construction-Plumbing

Colors
0054AA
0677BA
7BADD7
CADEEF
E8F1F8

Requirements
Must have
• Logo

```html
<!DOCTYPE html>
<html lang="en">
<head>
<meta charset="utf-8">
<title>Aquavelo – Z-fold plumbing flyer</title>
<link href="https://fonts.googleapis.com/css2?family=Poppins:wght@400;500;600;700;800&display=swap" rel="stylesheet">
<style>
:root{
  --navy:#1c2f62;
  --navy-deep:#17284f;
  --royal:#1f4a9c;
  --sky:#3ea2de;
  --sky-soft:#7badd7;
  --yellow:#f8b410;
  --red:#e5222b;
  --green:#4a9a3c;
  --white:#ffffff;
  --page:#e8e8e8;
}
*{box-sizing:border-box;margin:0;padding:0}
html,body{width:1200px;height:2461px;overflow:hidden;background:var(--page);font-family:"Poppins",sans-serif}
.sheet{position:absolute;left:50px;width:800px;height:620px;transform:scale(1.375);transform-origin:0 0;box-shadow:0 6px 18px rgba(0,0,0,.25);overflow:hidden}
.sheet--outside{top:253px}
.sheet--inside{top:1357px}
.panel{position:absolute;top:0;height:620px;overflow:hidden;color:var(--white)}
.panel--a{left:0;width:267px;background:var(--sky)}
.panel--b{left:267px;width:267px;background:var(--navy)}
.panel--c{left:534px;width:266px;background:var(--navy)}
.abs{position:absolute}
.swoosh{position:absolute;left:0;width:100%}

/* reviews */
.review-title{left:38px;top:28px;font-size:19px;font-weight:800;color:var(--navy);letter-spacing:.2px}
.review{left:38px;width:215px;border:1px solid rgba(255,255,255,.55);border-left:none;border-radius:0 8px 8px 0;padding:4px 8px 6px 8px}
.review .quote{position:absolute;left:-10px;top:-8px;font-size:26px;font-weight:800;color:var(--yellow);line-height:1}
.review .stars{color:var(--yellow);font-size:9px;letter-spacing:1px;line-height:1}
.review p{font-size:9.4px;line-height:1.12;color:var(--white)}
.review .author{position:absolute;left:2px;bottom:-16px;font-size:8.5px;font-weight:700;color:var(--navy)}
.illus{position:absolute}

/* contact panel */
.alert{left:18px;width:232px;height:56px;background:var(--white);border-radius:6px;overflow:hidden}
.alert .tab{position:absolute;left:0;top:0;width:64px;height:56px;background:var(--red);display:flex;align-items:center;justify-content:center}
.alert .txt{position:absolute;left:74px;top:6px}
.alert .head{font-size:11px;font-weight:700;color:var(--red);line-height:1.1}
.alert .pill{display:inline-block;margin:2px 0;background:var(--sky);color:var(--white);font-size:8px;font-weight:600;padding:0 8px;border-radius:3px;line-height:12px}
.alert .sub{font-size:10px;font-weight:700;color:var(--navy);line-height:1.2}
.brand{text-align:center;font-weight:800;color:var(--white);letter-spacing:.5px}
.brand-dot{border-radius:50%;background:var(--sky);border:3px solid var(--white)}
.cta-pill{background:var(--yellow);color:var(--navy);font-weight:800;border-radius:6px;text-align:center}
.contact-item{left:0;width:267px;text-align:center;font-size:10px;font-weight:500}
.contact-item svg{display:block;margin:0 auto 4px}
.contact-item.phone{font-size:15px;font-weight:700}

/* cover */
.cover-lead{left:0;width:266px;text-align:center;font-size:17px;font-weight:700;color:var(--sky);line-height:1}
.cover-big{left:0;width:266px;text-align:center;font-size:33px;font-weight:800;line-height:1.05}
.cover-big .y{color:var(--yellow)}
.cover-note{left:0;width:266px;text-align:center;font-size:10px;line-height:1.25}
.url-pill{background:var(--yellow);color:var(--navy);font-size:10.5px;font-weight:700;letter-spacing:1px;border-radius:4px;text-align:center;line-height:20px}

/* inside */
.section-title{font-size:19px;font-weight:800;line-height:1;color:var(--white)}
.section-title .y{color:var(--yellow)}
.rule{height:2px;background:var(--yellow)}
.rule::after{content:"";position:absolute;right:-3px;top:-2px;width:6px;height:6px;border-radius:50%;background:var(--yellow)}
.body-copy{font-size:9.6px;line-height:1.16;color:var(--white)}
.photo{border:2px solid var(--white)}
.service-card{left:62px;width:142px;height:110px;border-radius:10px;border:2px solid rgba(255,255,255,.7);overflow:hidden;text-align:center}
.service-card .art{position:absolute;left:0;top:0;width:100%;height:70px}
.service-card .label{position:absolute;left:0;bottom:8px;width:100%;font-size:11.5px;font-weight:700;line-height:1.15}
.service-card .label small{display:block;font-size:10px;font-weight:500}
.card-blue{background:linear-gradient(#53b8ef,#1a7fcf)}
.card-red{background:linear-gradient(#f26a3b,#d83a22)}
.card-green{background:linear-gradient(#6cbf57,#3c8c34)}
.icon-tile{width:80px;text-align:center;font-size:9.4px;font-weight:500;line-height:1.15}
.icon-tile svg{display:block;margin:0 auto 4px}
</style>
</head>
<body>

<svg width="0" height="0" style="position:absolute" aria-hidden="true">
  <defs>
    <symbol id="hex" viewBox="0 0 50 54">
      <polygon points="25,2 47,14 47,40 25,52 3,40 3,14" fill="#fff" stroke="#f8b410" stroke-width="3"/>
    </symbol>
    <symbol id="ico-phone" viewBox="0 0 24 24"><path d="M6.6 10.8c1.4 2.8 3.8 5.1 6.6 6.6l2.2-2.2c.3-.3.7-.4 1-.2 1.1.4 2.3.6 3.6.6.6 0 1 .4 1 1V20c0 .6-.4 1-1 1C10.6 21 3 13.4 3 4c0-.6.4-1 1-1h3.5c.6 0 1 .4 1 1 0 1.3.2 2.5.6 3.6.1.3 0 .7-.2 1z" fill="#1c2f62"/></symbol>
    <symbol id="ico-mail" viewBox="0 0 24 24"><rect x="3" y="6" width="18" height="12" rx="1.5" fill="#1c2f62"/><path d="M3.5 7l8.5 6 8.5-6" stroke="#fff" stroke-width="1.5" fill="none"/></symbol>
    <symbol id="ico-pin" viewBox="0 0 24 24"><path d="M12 2a7 7 0 0 0-7 7c0 5 7 13 7 13s7-8 7-13a7 7 0 0 0-7-7z" fill="#1c2f62"/><circle cx="12" cy="9" r="2.6" fill="#fff"/></symbol>
    <symbol id="ico-globe" viewBox="0 0 24 24"><circle cx="12" cy="12" r="9" fill="#1c2f62"/><path d="M3 12h18M12 3c3 3 3 15 0 18M12 3c-3 3-3 15 0 18" stroke="#fff" stroke-width="1.3" fill="none"/></symbol>
  </defs>
</svg>

<!-- OUTSIDE SPREAD -->
<section class="sheet sheet--outside">

  <div class="panel panel--a">
    <div class="abs review-title">CUSTOMER REVIEW</div>

    <div class="abs review" style="top:66px">
      <span class="quote">“</span>
      <div class="stars">★★★★★</div>
      <p>Stvarno jednostavni majstori. Imali smo problema sa odvodom već neko vrijeme. Snimili su je nabrzinu i detektirali nakupljenu masnoću. Očistili je posebnim strojem. Vjerujem da neće biti više problema.</p>
      <span class="author">-IVANA K</span>
    </div>

    <div class="abs review" style="top:180px">
      <span class="quote">“</span>
      <div class="stars">★★★★★</div>
      <p>Lorem Ipsum is simply dummy text of the printing and typesetting industry. Lorem Ipsum has been the industry's standard dummy text ever since the 1500s, when an unknown printer took a galley of type and scrambled it to make a type specimen book.</p>
      <span class="author">-MARK ELLIS</span>
    </div>

    <div class="abs review" style="top:298px">
      <span class="quote">“</span>
      <div class="stars">★★★★★</div>
      <p>Lorem Ipsum is simply dummy text of the printing and typesetting industry. Lorem Ipsum has been the industry's standard dummy text ever since the 1500s, when an unknown printer took a galley of type and scrambled it to make and type specimen book.</p>
      <span class="author">-MARK ELLIS</span>
    </div>

    <svg class="swoosh" style="top:410px" width="267" height="210" viewBox="0 0 267 210">
      <path d="M0 0 C60 40 170 60 267 30 L267 210 L0 210 Z" fill="#f8b410"/>
      <path d="M0 24 C70 62 170 76 267 44 L267 210 L0 210 Z" fill="#1c2f62"/>
    </svg>
    <div class="illus" role="img" aria-label="Mascot illustration of a plumber hero holding a wrench, inside a blue circle" style="left:72px;top:446px;width:132px;height:132px;border-radius:50%;border:4px solid #fff;background:radial-gradient(circle at 50% 40%,#5ab6ec,#1f63b8)"></div>
  </div>

  <div class="panel panel--b">
    <div class="abs alert" style="top:32px">
      <div class="tab">
        <svg width="34" height="34" viewBox="0 0 34 34"><circle cx="17" cy="17" r="14" fill="none" stroke="#fff" stroke-width="3"/><text x="17" y="22" text-anchor="middle" font-family="Poppins,sans-serif" font-weight="700" font-size="13" fill="#fff">24</text></svg>
      </div>
      <div class="txt">
        <div class="head">EMERGENCY PLUMBING</div>
        <span class="pill">CALL US NOW</span>
        <div class="sub">095-555-0148</div>
      </div>
    </div>

    <div class="abs alert" style="top:109px">
      <div class="tab">
        <svg width="34" height="28" viewBox="0 0 34 28"><rect x="2" y="4" width="30" height="22" rx="2" fill="none" stroke="#fff" stroke-width="2.5"/><path d="M3 6l14 10 14-10" stroke="#fff" stroke-width="2.5" fill="none"/></svg>
      </div>
      <div class="txt">
        <div class="head">QUICK CONTACT</div>
        <span class="pill">CONTACT US</span>
        <div class="sub">Leakage / Clogged?</div>
      </div>
    </div>

    <div class="abs brand-dot" style="left:113px;top:192px;width:40px;height:40px"></div>
    <div class="abs brand" style="left:0;top:236px;width:267px;font-size:17px">AQUAVELO</div>

    <div class="abs cta-pill" style="left:53px;top:307px;width:160px;height:26px;font-size:16px;line-height:26px">CONTACT US</div>

    <div class="abs contact-item phone" style="top:350px">
      <svg width="22" height="22" viewBox="0 0 22 22"><circle cx="11" cy="11" r="10" fill="#fff"/><use href="#ico-phone" x="5" y="5" width="12" height="12"/></svg>
      095-555-0148
    </div>
    <div class="abs contact-item" style="top:410px">
      <svg width="22" height="22" viewBox="0 0 22 22"><circle cx="11" cy="11" r="10" fill="#fff"/><use href="#ico-mail" x="5" y="5" width="12" height="12"/></svg>
      info@aquavelo-example.hr
    </div>
    <div class="abs contact-item" style="top:467px">
      <svg width="22" height="22" viewBox="0 0 22 22"><circle cx="11" cy="11" r="10" fill="#fff"/><use href="#ico-pin" x="5" y="5" width="12" height="12"/></svg>
      45 Harbor Lane,<br>Rivertown, State, 10245
    </div>
    <div class="abs contact-item" style="top:540px">
      <svg width="22" height="22" viewBox="0 0 22 22"><circle cx="11" cy="11" r="10" fill="#fff"/><use href="#ico-globe" x="5" y="5" width="12" height="12"/></svg>
      www.aquavelo-example.hr
    </div>
  </div>

  <div class="panel panel--c">
    <div class="abs" style="left:0;top:0;width:266px;height:380px;background:linear-gradient(#1f4a9c,#1b3d86)"></div>
    <div class="abs brand-dot" style="left:110px;top:28px;width:46px;height:46px"></div>
    <div class="abs brand" style="left:0;top:80px;width:266px;font-size:19px">AQUAVELO</div>
    <div class="illus" role="img" aria-label="Mascot illustration of a masked plumber hero carrying a pipe on his shoulder, giving a thumbs up" style="left:22px;top:160px;width:222px;height:200px;border-radius:18px;background:radial-gradient(ellipse at 50% 45%,#5ab6ec,#2a6fc4 70%,rgba(31,74,156,0))"></div>
    <svg class="swoosh" style="top:320px" width="266" height="300" viewBox="0 0 266 300">
      <path d="M0 70 C100 70 200 40 266 0 L266 300 L0 300 Z" fill="#f8b410"/>
      <path d="M0 82 C100 84 200 58 266 22 L266 300 L0 300 Z" fill="#1c2f62"/>
    </svg>
    <div class="abs cover-lead" style="top:428px">LET THE WATER</div>
    <div class="abs cover-big" style="top:447px"><span class="y">STAY IN THE</span><br>PIPES ONLY</div>
    <div class="abs cover-note" style="top:530px">We're open 24/7/365 because plumbing<br>emergencies don't wait ...</div>
    <div class="abs url-pill" style="left:58px;top:568px;width:150px">www.aquavelo-example.hr</div>
  </div>
</section>

<!-- INSIDE SPREAD -->
<section class="sheet sheet--inside">

  <div class="panel panel--a">
    <div class="illus" role="img" aria-label="Photograph of silver pipes running along a dark brick wall" style="left:0;top:0;width:267px;height:210px;background:linear-gradient(135deg,#d9d9d9,#6b6b6b 55%,#2b2b2b)"></div>
    <svg class="swoosh" style="top:90px" width="267" height="140" viewBox="0 0 267 140">
      <path d="M0 0 C20 70 110 120 267 100 L267 140 L0 140 Z" fill="#f8b410"/>
      <path d="M0 14 C30 80 120 124 267 110 L267 140 L0 140 Z" fill="#3ea2de"/>
    </svg>
    <div class="abs section-title" style="left:25px;top:236px;color:var(--navy)">PROFESSIONAL<br>PLUMBING SERVICES<br>IN STATE</div>
    <div class="abs rule" style="left:25px;top:300px;width:224px"></div>
    <div class="abs body-copy" style="left:27px;top:310px;width:222px">Lorem Ipsum is simply dummy text of the printing and typesetting industry. Lorem Ipsum has been the industry's standard dummy text ever since the 1500s, when an unknown printer took a galley of type and scrambled it to make a type specimen book. It has survived not only five centuries, but also the leap into electronic typesetting, remaining essentially unchanged. It was popularised in the 1960s with the release of Letraset sheets containing Lorem Ipsum passages, and more recently with desktop publishing software like Aldus PageMaker including versions of Lorem Ipsum.</div>
    <div class="abs photo" role="img" aria-label="Photograph of a rusty outdoor pipe in green grass" style="left:25px;top:482px;width:112px;height:86px;background:linear-gradient(#4d6b3a,#7f8f55 60%,#3c5a2c)"></div>
    <div class="abs photo" role="img" aria-label="Photograph of a brass tap dripping water against a yellow background" style="left:140px;top:482px;width:112px;height:86px;background:linear-gradient(135deg,#f7b21b,#e08a12)"></div>
  </div>

  <div class="panel panel--b">
    <div class="abs section-title" style="left:16px;top:26px;font-size:18px"><span class="y">AQUAVELO</span><br>SERVICES</div>
    <div class="abs rule" style="left:16px;top:68px;width:222px"></div>

    <div class="abs service-card card-blue" style="top:100px">
      <div class="art" role="img" aria-label="Mascot plumber hero illustration" style="background:radial-gradient(ellipse at 50% 60%,rgba(255,255,255,.35),rgba(255,255,255,0) 70%)"></div>
      <div class="label">PLUMBING<small>Services</small></div>
    </div>
    <div class="abs service-card card-red" style="top:240px">
      <div class="art" role="img" aria-label="Mascot plumber hero illustration" style="background:radial-gradient(ellipse at 50% 60%,rgba(255,255,255,.3),rgba(255,255,255,0) 70%)"></div>
      <div class="label">DRAIN<small>Cleaning</small></div>
    </div>
    <div class="abs service-card card-green" style="top:380px">
      <div class="art" role="img" aria-label="Mascot plumber hero illustration" style="background:radial-gradient(ellipse at 50% 60%,rgba(255,255,255,.3),rgba(255,255,255,0) 70%)"></div>
      <div class="label">LEAK<small>Detection</small></div>
    </div>

    <div class="abs body-copy" style="left:18px;top:536px;width:226px">There are many variations of passages of Lorem Ipsum available, but the majority have suffered alteration in some form, by injected humour, or randomised words which don't look even slightly believable.</div>
  </div>

  <div class="panel panel--c">
    <div class="abs section-title" style="left:16px;top:24px;font-size:18px"><span class="y">OUR FULL RANGE OF</span><br>PLUMBING SERVICES</div>
    <div class="abs rule" style="left:16px;top:66px;width:226px"></div>

    <div class="abs icon-tile" style="left:10px;top:90px"><svg width="48" height="52"><use href="#hex"/><path d="M18 16v12h12v8M22 30c0 3 4 3 4 0" stroke="#1c2f62" stroke-width="2.2" fill="none"/></svg>Leak<br>Detection</div>
    <div class="abs icon-tile" style="left:93px;top:90px"><svg width="48" height="52"><use href="#hex"/><rect x="16" y="16" width="10" height="8" fill="none" stroke="#1c2f62" stroke-width="2"/><path d="M16 26h18c0 6-4 10-10 10l-2 4" stroke="#1c2f62" stroke-width="2" fill="none"/></svg>Toilet Repair<br>&amp; Installation</div>
    <div class="abs icon-tile" style="left:176px;top:90px"><svg width="48" height="52"><use href="#hex"/><rect x="14" y="22" width="22" height="12" fill="none" stroke="#1c2f62" stroke-width="2"/><path d="M20 22v-6M30 22v-6" stroke="#1c2f62" stroke-width="2"/></svg>Gas Lines</div>

    <div class="abs icon-tile" style="left:10px;top:188px"><svg width="48" height="52"><use href="#hex"/><path d="M16 14v22h18M22 20v10h8" stroke="#1c2f62" stroke-width="2" fill="none"/></svg>Drain<br>Cleaning</div>
    <div class="abs icon-tile" style="left:93px;top:188px"><svg width="48" height="52"><use href="#hex"/><path d="M12 28h26M25 18v10M20 18h10" stroke="#1c2f62" stroke-width="2.2" fill="none"/><circle cx="25" cy="28" r="4" fill="#1c2f62"/></svg>Gas Valves</div>
    <div class="abs icon-tile" style="left:176px;top:188px"><svg width="48" height="52"><use href="#hex"/><path d="M28 14v10c0 6-10 6-10 0v-2" stroke="#1c2f62" stroke-width="2.4" fill="none"/><path d="M24 32c0 4 2 6 2 6" stroke="#1c2f62" stroke-width="2"/></svg>Drain<br>Repair</div>

    <div class="abs icon-tile" style="left:10px;top:286px"><svg width="48" height="52"><use href="#hex"/><path d="M18 14h10v6M20 24h14l-3-4h-8z" stroke="#1c2f62" stroke-width="2" fill="none"/><path d="M22 28v3M26 28v5M30 28v3" stroke="#1c2f62" stroke-width="1.6"/></svg>Shower Repair<br>&amp; Installation</div>
    <div class="abs icon-tile" style="left:93px;top:286px"><svg width="48" height="52"><use href="#hex"/><path d="M20 14v12h10v12" stroke="#1c2f62" stroke-width="3" fill="none"/><path d="M30 22l4-2M32 26l4 1" stroke="#1c2f62" stroke-width="1.6"/></svg>Burst Pipes</div>
    <div class="abs icon-tile" style="left:176px;top:286px"><svg width="48" height="52"><use href="#hex"/><path d="M16 18l18 18M34 18L16 36" stroke="#1c2f62" stroke-width="2.6"/></svg>Rooter<br>Services</div>

    <div class="abs icon-tile" style="left:10px;top:384px"><svg width="48" height="52"><use href="#hex"/><rect x="16" y="18" width="18" height="14" fill="none" stroke="#1c2f62" stroke-width="2"/><path d="M18 36h14" stroke="#1c2f62" stroke-width="2"/></svg>Garbage<br>Disposals</div>
    <div class="abs icon-tile" style="left:93px;top:384px"><svg width="48" height="52"><use href="#hex"/><path d="M18 16h10v10h6v10" stroke="#1c2f62" stroke-width="3" fill="none"/></svg>Pipe Repair</div>
    <div class="abs icon-tile" style="left:176px;top:384px"><svg width="48" height="52"><use href="#hex"/><path d="M14 24h8l4-4h10M14 30h22" stroke="#1c2f62" stroke-width="2.2" fill="none"/><circle cx="26" cy="30" r="3" fill="#1c2f62"/></svg>Plumbing<br>Repairs</div>

    <div class="abs icon-tile" style="left:45px;top:482px"><svg width="48" height="52"><use href="#hex"/><rect x="18" y="14" width="14" height="24" rx="2" fill="none" stroke="#1c2f62" stroke-width="2"/><circle cx="25" cy="22" r="3" fill="#1c2f62"/></svg>Water Heaters</div>
    <div class="abs icon-tile" style="left:140px;top:482px"><svg width="48" height="52"><use href="#hex"/><path d="M12 28h26" stroke="#1c2f62" stroke-width="3"/><rect x="20" y="21" width="10" height="14" fill="none" stroke="#1c2f62" stroke-width="2"/><path d="M25 16v5" stroke="#1c2f62" stroke-width="2"/></svg>Pipelining</div>
  </div>
</section>

</body>
</html>
```